Velk Consulting -New consulting business in architecture, urban planning, and real estate development

We need a stationery design, including logo, business cards, etc, work for a new consulting business that works in the world of architectural, urban planning and real estate development.

The name of the company is "Velk Consulting". Velk is my last name but it of course also has the meaning 'cool' and 'hip'.

Target Market(s)

The business will provide boutique consulting services to high end clients that may include property developers, cities, etc.

Industry/Entity Type

Consultant

Contact Information for Business Card

VELK Consulting
First Name Last Name
Title
Phone number
Address
Website
Optional: Twitter handle

Logo Text

VELK Consulting

Font styles to use
Sans Serif

Colors

Designer to choose colors to be used in the design.

Requirements
Must have
• Simple design
• Easy to read font
• Modern
• Elegance
• Nice font that can be used for future reports, letters, etc.
• Good colour scheme that allows for the elegance to come through
Should not have
• Complex design ideas
• Complex logos
• Not a corporate feel and look

```html
<!DOCTYPE html>
<html lang="en">
<head>
<meta charset="utf-8">
<title>Velk Consulting – Letterhead</title>
<link rel="stylesheet" href="https://fonts.googleapis.com/css2?family=Roboto:wght@400;500&display=swap">
<style>
  :root {
    --backdrop: #e9e9ea;
    --paper: #f3f3f4;
    --gold: #a07f1e;
    --ink: #2b2b2b;
    --body-text: #6b6b6b;
    --divider: #b9b9b9;
  }
  * { box-sizing: border-box; margin: 0; padding: 0; }
  html, body {
    width: 1200px; height: 1129px; overflow: hidden;
    background: var(--backdrop);
    font-family: "Roboto", Arial, sans-serif;
  }
  .letterhead {
    position: absolute; left: 214px; top: 22px;
    width: 772px; height: 1085px;
    background: var(--paper);
    box-shadow: 0 1px 3px rgba(0,0,0,.12);
  }
  .letterhead__frame {
    position: absolute; left: 26px; top: 23px; right: 26px; bottom: 23px;
    border: 1.5px solid var(--gold);
  }
  .brand {
    position: absolute; left: 0; right: 0; top: 92px;
    text-align: center;
    color: var(--gold);
    font-weight: 500; font-size: 30px; letter-spacing: 6px;
    text-transform: uppercase;
  }
  .recipient {
    position: absolute; left: 88px; top: 300px;
    font-size: 14.5px; line-height: 17.5px; color: var(--body-text);
    letter-spacing: .3px;
  }
  .recipient__name, .recipient__title { color: var(--ink); font-weight: 500; }
  .letter-date {
    position: absolute; right: 73px; top: 356px;
    font-size: 14.5px; color: var(--ink); letter-spacing: .4px;
  }
  .letter-body {
    position: absolute; left: 69px; top: 436px; width: 634px;
    font-size: 11.4px; line-height: 23.2px; color: var(--body-text);
    letter-spacing: .35px; text-align: justify;
  }
  .letter-body p { text-indent: 18px; margin-bottom: 23px; }
  .company-footer {
    position: absolute; left: 0; right: 0; top: 988px;
    text-align: center; font-size: 11px; color: var(--ink);
  }
  .company-footer strong { font-weight: 500; }
  .contact-row {
    margin-top: 10px;
    display: flex; justify-content: center; align-items: center;
  }
  .contact-item { display: flex; align-items: center; gap: 6px; padding: 0 9px; }
  .contact-item + .contact-item { border-left: 1px solid var(--divider); }
  .contact-item svg { width: 13px; height: 13px; stroke: var(--gold); fill: none; stroke-width: 1.3; }
  .contact-row { line-height: 22px; }
</style>
</head>
<body>
<main class="letterhead">
  <div class="letterhead__frame"></div>

  <div class="brand">Velk Consulting</div>

  <address class="recipient" style="font-style:normal">
    <div class="recipient__name">MR. Daniel HARPER</div>
    <div class="recipient__title">Managing Director</div>
    <div>12/08 Linden Court</div>
    <div>Oregon - 974015532</div>
  </address>

  <div class="letter-date">Date : 01 July 2018</div>

  <section class="letter-body">
    <p>Lorem ipsum dolor sit amet, justo platonem in per, dicant constituto ne eam. Aeque persecuti sit ea, at vis commodo tractatos vituperata, sea an albucius forensibus. Wisi quodsi id qui, duo tempor aliquam assentior eu, no diceret tibique definiebas mei. Id nec noster facilisi mandamus.</p>
    <p>Nullam definiebas signiferumque pro te, vel mutat lobortis conceptam in. Usu justo minimum an, ne regione sanctus praesent usu, eam ut adipisci volutpat. Vel odio tibique consequat ne, in dicit gubergren appellantur vis, quo ei omnis elitr. Qui ne enim dictas dissentiet, pro nulla quodsi deseruisse te. Vide prima eloquentiam pro ei, agam dicta in pro, eu persius propriae constituam sea. Ius ut iriure oblique laboramus, cu sed fugit commune invenire, viris repudiandae ex vis.Nullam definiebas signiferumque pro te, vel mutat lobortis conceptam in. Usu justo minimum an, ne regione sanctus praesent usu, eam ut adipisci volutpat. Vel odio tibique consequat ne, in dicit gubergren appellantur vis, quo ei omnis elitr. Qui ne enim dictas dissentiet, pro nulla quodsi deseruisse te. Vide prima eloquentiam pro ei, agam dicta in pro, eu persius propriae constituam sea. Ius ut iriure oblique laboramus, cu sed fugit commune invenire, viris repudiandae ex vis.Nullam definiebas signiferumque pro te, vel mutat lobortis conceptam in. Usu justo minimum an, ne regione sanctus praesent usu, eam ut adipisci volutpat. Vel odio tibique consequat ne, in dicit gubergren appellantur vis, quo ei omnis elitr. Qui ne enim dictas dissentiet, pro nulla quodsi deseruisse te. Vide prima eloquentiam pro ei, agam dicta in pro, eu persius propriae constituam sea. Ius ut iriure oblique laboramus, cu sed fugit commune invenire, viris repudiandae ex vis.</p>
  </section>

  <footer class="company-footer">
    <div><strong>Velk Consulting</strong> - 214 N Alder Avenue, Corvale, OR 97401</div>
    <div class="contact-row">
      <span class="contact-item">
        <svg viewBox="0 0 16 16" aria-hidden="true"><path d="M3 1.5l2.5 0 1.2 3.3-1.6 1.2a8 8 0 0 0 4.9 4.9l1.2-1.6 3.3 1.2 0 2.5c0 .6-.5 1-1 1A12.5 12.5 0 0 1 2 2.5c0-.5.4-1 1-1z"/></svg>
        000 000 0000
      </span>
      <span class="contact-item">
        <svg viewBox="0 0 16 16" aria-hidden="true"><rect x="1" y="3" width="14" height="10"/><path d="M1 3l7 6 7-6"/></svg>
        info@velkconsulting.com
      </span>
      <span class="contact-item">
        <svg viewBox="0 0 16 16" aria-hidden="true"><circle cx="8" cy="8" r="6.5"/><ellipse cx="8" cy="8" rx="3" ry="6.5"/><path d="M1.5 8h13M2.5 4.8h11M2.5 11.2h11"/></svg>
        www.velkconsulting.com
      </span>
    </div>
  </footer>
</main>
</body>
</html>
```